Business Card Design

New business card design

Target Market(s)

Residential & Commercial Property Managers

Industry/Entity Type

Plumbing Services

Contact Information for Business Card

Name - Rowan Keddle, title - Director, Phone Number - 0431 286 517, email - rowan@tbk-plumbing.com.au, Company ABN - 73 215 904 386,

Font styles to use
Sans Serif

Colors
0054AA
0677BA
7BADD7
CADEEF
E8F1F8

```html
<!DOCTYPE html>
<html lang="en">
<head>
<meta charset="utf-8">
<title>TBK Plumbing Services – Business Card</title>
<link rel="stylesheet" href="https://fonts.googleapis.com/css2?family=Roboto:wght@300;400;700&display=swap">
<style>
  :root {
    --stage: #ececec;
    --card-white: #ffffff;
    --brand-blue: #0aa6e6;
    --brand-blue-deep: #0677ba;
    --brand-blue-light: #7badd7;
    --ink-dark: #1f242a;
    --ink-grey: #4a4f55;
    --shadow: rgba(0, 0, 0, 0.18);
  }
  * { box-sizing: border-box; margin: 0; padding: 0; }
  html, body {
    width: 1200px;
    height: 900px;
    overflow: hidden;
    background: var(--stage);
    font-family: "Roboto", Arial, sans-serif;
  }
  .stage {
    width: 1200px;
    height: 900px;
    display: flex;
    align-items: center;
    justify-content: center;
    gap: 40px;
  }
  .card {
    position: relative;
    width: 540px;
    height: 310px;
    border-radius: 22px;
    overflow: hidden;
    box-shadow: 0 14px 30px var(--shadow);
  }
  .card__art {
    position: absolute;
    inset: 0;
    width: 100%;
    height: 100%;
  }

  /* Front */
  .card--front { background: var(--card-white); }
  .brand {
    position: absolute;
    left: 34px;
    top: 30px;
    display: flex;
    align-items: center;
    gap: 10px;
  }
  .brand__mark {
    width: 14px;
    height: 14px;
    background: var(--brand-blue);
  }
  .brand__name {
    font-weight: 300;
    font-size: 30px;
    letter-spacing: 1px;
    color: var(--ink-dark);
  }
  .contact {
    position: absolute;
    left: 34px;
    top: 100px;
    color: var(--ink-grey);
    font-size: 15px;
    line-height: 1.45;
  }
  .contact__name {
    font-weight: 700;
    font-size: 20px;
    color: var(--brand-blue);
    text-transform: uppercase;
    letter-spacing: 0.3px;
  }
  .contact__title { font-size: 14px; margin-bottom: 10px; }
  .contact__label { color: var(--brand-blue); }
  .contact__row { display: flex; align-items: center; gap: 7px; }
  .contact__icon { width: 13px; height: 13px; fill: var(--ink-grey); }

  /* Back */
  .card--back {
    background: linear-gradient(160deg, #22b0ea 0%, var(--brand-blue) 60%, #0a9cdc 100%);
  }
  .back-brand {
    position: absolute;
    left: 46px;
    top: 62px;
    color: var(--card-white);
    font-weight: 300;
    font-size: 36px;
    letter-spacing: 1px;
  }
</style>
</head>
<body>
<main class="stage">

  <section class="card card--front" aria-label="Business card front">
    <svg class="card__art" viewBox="0 0 540 310" role="img" aria-label="Blue and dark curved corner panels">
      <path d="M300 310 C320 210 410 130 540 72 C478 112 438 200 418 310 Z" fill="var(--brand-blue)"/>
      <path d="M540 72 C478 112 438 200 418 310 L540 310 Z" fill="var(--ink-dark)"/>
      <path d="M540 72 C478 112 438 200 418 310" fill="none" stroke="var(--card-white)" stroke-width="5"/>
    </svg>

    <div class="brand">
      <span class="brand__mark"></span>
      <span class="brand__name">TBK Plumbing Services</span>
    </div>

    <div class="contact">
      <p class="contact__name">Rowan Keddle</p>
      <p class="contact__title">Director</p>
      <p><span class="contact__label">ABN:</span> 73 215 904 386</p>
      <p class="contact__row">
        <svg class="contact__icon" viewBox="0 0 24 24" aria-hidden="true"><path d="M6.6 10.8a15.1 15.1 0 0 0 6.6 6.6l2.2-2.2a1 1 0 0 1 1-.25 11.4 11.4 0 0 0 3.6.57 1 1 0 0 1 1 1V20a1 1 0 0 1-1 1A17 17 0 0 1 3 4a1 1 0 0 1 1-1h3.5a1 1 0 0 1 1 1c0 1.25.2 2.45.57 3.57a1 1 0 0 1-.25 1z"/></svg>
        0431 286 517
      </p>
      <p class="contact__row">
        <svg class="contact__icon" viewBox="0 0 24 24" aria-hidden="true"><path d="M2 5h20v14H2z M2 5l10 8 10-8" fill="none" stroke="var(--ink-grey)" stroke-width="2"/></svg>
        rowan@tbk-plumbing.com.au
      </p>
    </div>
  </section>

  <section class="card card--back" aria-label="Business card back">
    <svg class="card__art" viewBox="0 0 540 310" role="img" aria-label="Soft translucent curved panel">
      <path d="M280 310 C310 230 410 160 540 128 L540 310 Z" fill="rgba(255,255,255,0.14)"/>
      <path d="M380 310 C400 250 460 200 540 178 L540 310 Z" fill="rgba(6,119,186,0.35)"/>
    </svg>
    <p class="back-brand">TBK Plumbing Services</p>
  </section>

</main>
</body>
</html>
```